Verdant Systems Business Card

want the back of card to be blue- with the logo in the center
front of card- info plus logo (info being mailing address, email address, and website address )
4 different names with titles to have on cards
1) Calvin Borsted - Owner
2) Naomi Trelvik- Customer Relationship Specialist
3) Felix Andrade- Vice President of Sales
4) Owen Markby- Chief Technology Officer

Target Market(s)

tech company in the government/probation office industry

Industry/Entity Type

Government Office

Contact Information for Business Card

1) Calvin Borsted - Owner

Colors
0355a3
ffffff

Requirements
Must have
• back side should be blue, with the logo placed in the center
• front side needs to include both the logo, as well as company info (info should include website address, email address, and mailing address)

```html
<!DOCTYPE html>
<html lang="en">
<head>
<meta charset="utf-8">
<title>Verdant Systems Business Card</title>
<link href="https://fonts.googleapis.com/css2?family=Open+Sans:wght@400;700&family=Roboto:wght@700&display=swap" rel="stylesheet">
<style>
  :root {
    --navy: #1b2d55;
    --grey-band: #86888b;
    --stage: #c5c8cb;
    --paper: #ffffff;
    --ink: #3f4246;
  }
  * { margin: 0; padding: 0; box-sizing: border-box; }
  html, body { width: 1200px; height: 900px; overflow: hidden; }
  body {
    position: relative;
    background: var(--stage);
    font-family: "Open Sans", Arial, sans-serif;
  }
  .card-front {
    position: absolute;
    left: 53px;
    width: 460px;
    height: 264px;
    background: var(--paper);
    overflow: hidden;
  }
  .card-front--owner { top: 34px; }
  .card-front--crs { top: 327px; }
  .card-front--vp { top: 620px; left: 55px; width: 456px; height: 258px; }

  .brand {
    position: absolute;
    right: 18px;
    top: 52px;
    display: flex;
    align-items: center;
    gap: 8px;
    color: var(--navy);
    font-weight: 700;
    font-size: 22px;
    letter-spacing: 0.5px;
    text-transform: uppercase;
  }
  .brand-dot {
    width: 14px; height: 14px;
    border-radius: 50%;
    background: var(--navy);
  }
  .person {
    position: absolute;
    left: 26px;
    top: 116px;
    color: var(--navy);
  }
  .person-name { font-size: 15px; font-weight: 700; line-height: 20px; }
  .person-title { font-size: 12px; color: var(--ink); line-height: 18px; }
  .rule {
    position: absolute;
    left: 26px; right: 18px;
    top: 159px;
    height: 1px;
    background: var(--navy);
  }
  .contacts {
    position: absolute;
    left: 26px;
    top: 168px;
    list-style: none;
    font-size: 11.5px;
    color: var(--ink);
    line-height: 17px;
  }
  .contacts li { display: flex; align-items: center; gap: 7px; }
  .contacts svg { width: 9px; height: 9px; fill: var(--navy); }
  .address {
    position: absolute;
    right: 18px;
    top: 188px;
    text-align: right;
    font-size: 11.5px;
    line-height: 14px;
    color: var(--ink);
    font-style: normal;
  }
  .band {
    position: absolute;
    left: 0; bottom: 0;
    width: 100%;
    height: 34px;
  }
  .band svg { position: absolute; inset: 0; width: 100%; height: 100%; }
  .website {
    position: absolute;
    right: 18px;
    top: 6px;
    font-size: 11.5px;
    color: var(--paper);
  }

  .card-back {
    position: absolute;
    left: 582px;
    top: 293px;
    width: 570px;
    height: 327px;
    background: var(--navy);
    display: flex;
    align-items: center;
    justify-content: center;
    gap: 14px;
    color: var(--paper);
  }
  .card-back .brand-dot { width: 30px; height: 30px; background: var(--paper); }
  .card-back-name {
    font-weight: 700;
    font-size: 36px;
    letter-spacing: 1px;
    text-transform: uppercase;
  }

  .offer-note {
    position: absolute;
    left: 575px;
    top: 716px;
    width: 600px;
    font-family: "Roboto", Arial, sans-serif;
    font-weight: 700;
    font-size: 21.5px;
    line-height: 27px;
    color: var(--navy);
  }
</style>
</head>
<body>

<svg width="0" height="0" style="position:absolute" aria-hidden="true">
  <symbol id="icon-phone" viewBox="0 0 10 10"><path d="M2 0.5 L3.6 2.6 L2.7 3.6 C3.3 5 4.8 6.6 6.3 7.3 L7.4 6.4 L9.5 8 L8.4 9.5 C4.5 9.3 0.7 5.5 0.5 1.6 Z"/></symbol>
  <symbol id="icon-mobile" viewBox="0 0 10 10"><path d="M2.5 0 H7.5 V10 H2.5 Z M3.5 1 V8 H6.5 V1 Z"/></symbol>
  <symbol id="icon-mail" viewBox="0 0 10 10"><path d="M0 1.5 H10 V8.5 H0 Z M1 2.5 L5 5.5 L9 2.5 Z"/></symbol>
</svg>

<section class="card-front card-front--owner">
  <div class="brand"><span class="brand-dot"></span>Verdant Systems</div>
  <div class="person">
    <p class="person-name">Calvin Borsted</p>
    <p class="person-title">Owner</p>
  </div>
  <div class="rule"></div>
  <ul class="contacts">
    <li><svg><use href="#icon-phone"/></svg>555-014-2283</li>
    <li><svg><use href="#icon-mobile"/></svg>555-014-7730(office)</li>
    <li><svg><use href="#icon-mail"/></svg>mara@verdantsystems.net</li>
  </ul>
  <address class="address">Harlow Crossing<br>Fenwick Dale, 2407</address>
  <div class="band">
    <svg viewBox="0 0 460 34" preserveAspectRatio="none">
      <path d="M0 5 H245 C238 9 234 13 224 13 H0 Z" fill="var(--grey-band)"/>
      <path d="M0 18 H228 C250 18 255 0 280 0 H460 V34 H0 Z" fill="var(--navy)"/>
    </svg>
    <span class="website">www.verdantsystems.net</span>
  </div>
</section>

<section class="card-front card-front--crs">
  <div class="brand"><span class="brand-dot"></span>Verdant Systems</div>
  <div class="person">
    <p class="person-name">Naomi Trelvik</p>
    <p class="person-title">Customer Relationship Specialist</p>
  </div>
  <div class="rule"></div>
  <ul class="contacts">
    <li><svg><use href="#icon-phone"/></svg>555-014-2283</li>
    <li><svg><use href="#icon-mobile"/></svg>555-014-7730(office)</li>
    <li><svg><use href="#icon-mail"/></svg>mara@verdantsystems.net</li>
  </ul>
  <address class="address">Harlow Crossing<br>Fenwick Dale, 2407</address>
  <div class="band">
    <svg viewBox="0 0 460 34" preserveAspectRatio="none">
      <path d="M0 5 H245 C238 9 234 13 224 13 H0 Z" fill="var(--grey-band)"/>
      <path d="M0 18 H228 C250 18 255 0 280 0 H460 V34 H0 Z" fill="var(--navy)"/>
    </svg>
    <span class="website">www.verdantsystems.net</span>
  </div>
</section>

<section class="card-front card-front--vp">
  <div class="brand"><span class="brand-dot"></span>Verdant Systems</div>
  <div class="person">
    <p class="person-name">Felix Andrade</p>
    <p class="person-title">Vice President of Sales</p>
  </div>
  <div class="rule"></div>
  <ul class="contacts">
    <li><svg><use href="#icon-phone"/></svg>555-014-2283</li>
    <li><svg><use href="#icon-mobile"/></svg>555-014-7730(office)</li>
    <li><svg><use href="#icon-mail"/></svg>mara@verdantsystems.net</li>
  </ul>
  <address class="address">Harlow Crossing<br>Fenwick Dale, 2407</address>
  <div class="band">
    <svg viewBox="0 0 460 34" preserveAspectRatio="none">
      <path d="M0 5 H245 C238 9 234 13 224 13 H0 Z" fill="var(--grey-band)"/>
      <path d="M0 18 H228 C250 18 255 0 280 0 H460 V34 H0 Z" fill="var(--navy)"/>
    </svg>
    <span class="website">www.verdantsystems.net</span>
  </div>
</section>

<section class="card-back">
  <span class="brand-dot"></span>
  <span class="card-back-name">Verdant Systems</span>
</section>

<p class="offer-note">I have made this card by using 3 different name . If you want i will make the card 4 different name and provide you all editable and print ready file.</p>

</body>
</html>
```